Business Recognition Design

We need a design for a recognition to be given to business leaders in our community.
The recognition shall be made on a brass plaque on wood panel background (picture attached, please use it as a background), and all drawing must be in vectors and only one color (black).
It should also have a logo on the top and signature on the right bottom.
The text is enclosed in DOC file.
Updates

Reason: just to be able to find the best solution

Reason: None of the suggestion is good enough. Logo in general is too big in comparison with the rest of the plate.

Industry/Entity Type

Business

Requirements
Must have
• - standard Windows font (or possibility to install the same font on Windows), as the name on the recognition shall be printed in the same font
Nice to have
• - some graphic element (in curves) representing achievements in business
- should look great :)

```html
<!DOCTYPE html>
<html lang="en">
<head>
<meta charset="utf-8">
<title>Recognition Plaque – Best Entrepreneur 2013</title>
<link rel="stylesheet" href="https://fonts.googleapis.com/css2?family=Ubuntu:wght@400;500;700&display=swap">
<style>
  :root {
    --wood-dark: #4a2412;
    --wood-mid: #6e3a1e;
    --wood-light: #8a4f2c;
    --brass-deep: #b8891c;
    --brass-mid: #dcb238;
    --brass-light: #f4d774;
    --screw-dark: #7a5a10;
    --screw-light: #f2d46a;
    --ink: #141414;
    --page: #ffffff;
  }
  * { margin: 0; padding: 0; box-sizing: border-box; }
  html, body {
    width: 1200px;
    height: 932px;
    overflow: hidden;
    background: var(--page);
  }
  .plaque {
    position: relative;
    width: 1200px;
    height: 932px;
    font-family: "Ubuntu", Arial, sans-serif;
    color: var(--ink);
  }
  .plaque__backing {
    position: absolute;
    inset: 0;
  }
  .plaque__content {
    position: absolute;
    inset: 0;
    text-align: center;
  }
  .logo-label {
    position: absolute;
    top: 108px;
    left: 0; right: 0;
    font-size: 45px;
    font-weight: 400;
  }
  .logo-rule {
    position: absolute;
    top: 196px;
    left: 403px;
    width: 394px;
    height: 4px;
    background: var(--ink);
  }
  .award-title {
    position: absolute;
    top: 212px;
    left: 0; right: 0;
    font-weight: 700;
    line-height: 1;
  }
  .award-title span { display: block; }
  .award-title__kicker { font-size: 53px; letter-spacing: 1px; }
  .award-title__main { font-size: 84px; margin-top: 4px; }
  .award-title__field { font-size: 58px; margin-top: 6px; letter-spacing: 1px; }
  .award-title__year { font-size: 92px; margin-top: 2px; letter-spacing: 2px; }
  .award-to {
    position: absolute;
    top: 528px;
    left: 0; right: 0;
    font-size: 28px;
  }
  .recipient {
    position: absolute;
    top: 572px;
    left: 0; right: 0;
    font-size: 45px;
    font-weight: 400;
  }
  .recipient strong { font-weight: 700; }
  .citation {
    position: absolute;
    top: 645px;
    left: 0; right: 0;
    font-size: 28px;
    line-height: 38px;
  }
  .citation strong { font-weight: 700; }
  .award-date, .signatory {
    position: absolute;
    top: 803px;
    font-size: 26px;
  }
  .award-date { left: 247px; }
  .award-date sup { font-size: 15px; vertical-align: 11px; }
  .signatory { left: 806px; }
</style>
</head>
<body>
  <div class="plaque">
    <svg class="plaque__backing" width="1200" height="932" viewBox="0 0 1200 932" aria-hidden="true">
      <defs>
        <linearGradient id="wood" x1="0" y1="0" x2="1" y2="1">
          <stop offset="0" stop-color="var(--wood-light)"/>
          <stop offset="0.5" stop-color="var(--wood-mid)"/>
          <stop offset="1" stop-color="var(--wood-dark)"/>
        </linearGradient>
        <linearGradient id="brass" x1="0" y1="0" x2="1" y2="1">
          <stop offset="0" stop-color="var(--brass-mid)"/>
          <stop offset="0.35" stop-color="var(--brass-light)"/>
          <stop offset="0.7" stop-color="var(--brass-mid)"/>
          <stop offset="1" stop-color="var(--brass-deep)"/>
        </linearGradient>
        <linearGradient id="bevel" x1="0" y1="0" x2="1" y2="1">
          <stop offset="0" stop-color="var(--brass-light)"/>
          <stop offset="1" stop-color="var(--brass-deep)"/>
        </linearGradient>
        <radialGradient id="screw" cx="0.4" cy="0.35" r="0.7">
          <stop offset="0" stop-color="var(--screw-light)"/>
          <stop offset="1" stop-color="var(--screw-dark)"/>
        </radialGradient>
      </defs>
      <rect class="wood-panel" x="0" y="0" width="1200" height="932" rx="6" fill="url(#wood)"/>
      <rect class="brass-bevel" x="40" y="46" width="1120" height="840" fill="url(#bevel)"/>
      <rect class="brass-face" x="50" y="56" width="1100" height="820" fill="url(#brass)"/>
      <g class="screws" fill="url(#screw)" stroke="var(--screw-dark)" stroke-width="2">
        <circle cx="88" cy="86" r="14"/>
        <circle cx="1125" cy="86" r="14"/>
        <circle cx="88" cy="838" r="14"/>
        <circle cx="1125" cy="838" r="14"/>
      </g>
    </svg>

    <div class="plaque__content">
      <div class="logo-label">logo</div>
      <div class="logo-rule"></div>

      <h1 class="award-title">
        <span class="award-title__kicker">RECOGNITION</span>
        <span class="award-title__main">The Best</span>
        <span class="award-title__field">Entrepreneur</span>
        <span class="award-title__year">in 2013</span>
      </h1>

      <p class="award-to">to</p>
      <p class="recipient">Mr. <strong>Daniel R. Whitford,</strong> MBA</p>

      <p class="citation">
        Under the leadership of Mr. Daniel R. Whitford, MBA<br>
        the company <strong>DR-WHITFORD Ltd</strong> has been selected<br>
        by a City Council as the best company of The City.
      </p>

      <p class="award-date">4<sup>th</sup> July, 2013</p>
      <p class="signatory">City Mayor</p>
    </div>
  </div>
</body>
</html>
```